Design and Renovation Company Luxury Business Card

I want to create a luxury business card for a Design and Renovation Firm . We will use our current logo. The company name is 528BUILDA. We do not want anything standard. We need a very unique concept.
Please see uploaded inspiration. I really like the textured paper option. I would like the card to be thick with debossing, and/or embossing options. The logo has orange in it but I would like to see the card with and without the orange. I think the orange may make the company feel less high-end. The goal is to elevate the logo not match its vibe per se of the logo. We want something very unique, not standard at all!
I would like a space for :
Logo,
Name,
Position,
Email,
Office number,
Website Address,
Business Address,
Thank you!
Have fun!
Target Market(s)
Home owners Age 35 +
Industry/Entity Type
Design and Renovation
Contact Information for Business Card
Logo, Name, Position, Email, Office number, Website Address, Business Address,.
Colors
Designer to choose colors to be used in the design.
Requirements
Must have
- A luxury designer feel. Must be black or dark grey but open to other luxury ideas.
Nice to have
- Gold, silver, black embossing or debossing. Textured paper design.
Should not have
- A cheap look and feel.

```html
<!DOCTYPE html>
<html lang="en">
<head>
<meta charset="utf-8">
<title>528BUILDA Business Card</title>
<link href="https://fonts.googleapis.com/css2?family=Nunito:wght@400;600;800&display=swap" rel="stylesheet">
<style>
  :root {
    --backdrop: #9b9c97;
    --card-black: #0d0d0d;
    --card-mid: #1f1f1f;
    --gold: #d8b56a;
    --gold-line: #b8954f;
  }
  * { margin: 0; padding: 0; box-sizing: border-box; }
  html, body { width: 1200px; height: 1200px; overflow: hidden; }
  body {
    background: var(--backdrop);
    position: relative;
    font-family: "Nunito", sans-serif;
    color: var(--gold);
  }
  .card {
    position: absolute;
    left: 150px;
    width: 900px;
    height: 516px;
    border: 3px solid var(--gold);
    box-shadow: 0 18px 40px rgba(0,0,0,0.35);
    overflow: hidden;
  }
  .card--front { top: 54px; }
  .card--back { top: 630px; }
  .card__texture {
    position: absolute; inset: 0;
    background: radial-gradient(ellipse at 50% 20%, var(--card-mid) 0%, #161616 45%, var(--card-black) 100%);
  }
  .card__frame {
    position: absolute; inset: 24px;
    border: 1px solid var(--gold-line);
  }
  .brand {
    position: absolute;
    left: 0; right: 0; top: 200px;
    display: flex; flex-direction: column; align-items: center;
  }
  .brand__name {
    font-weight: 600;
    font-size: 64px;
    line-height: 1;
    letter-spacing: 4px;
  }
  .brand__tagline {
    margin-top: 14px;
    font-weight: 400;
    font-size: 18px;
    letter-spacing: 3.4px;
  }
  .website {
    position: absolute;
    right: 68px; bottom: 52px;
    font-size: 21px;
    letter-spacing: 0.4px;
  }
  .person {
    position: absolute;
    left: 530px; top: 52px;
  }
  .person__name {
    font-weight: 800;
    font-size: 44px;
    letter-spacing: 3px;
    padding-bottom: 2px;
    border-bottom: 2px solid var(--gold);
    display: inline-block;
  }
  .person__title {
    font-weight: 800;
    font-size: 17px;
    margin-top: 6px;
  }
  .contacts {
    position: absolute;
    left: 530px; top: 238px;
    list-style: none;
  }
  .contacts__item {
    display: flex; align-items: flex-start; gap: 16px;
    font-size: 22px;
    letter-spacing: 2px;
    line-height: 25px;
    margin-bottom: 14px;
  }
  .contacts__icon { width: 28px; height: 28px; flex: none; margin-top: -1px; }
  .back-brand {
    position: absolute;
    left: 90px; top: 360px;
    width: 250px;
    text-align: center;
    font-weight: 600;
    font-size: 32px;
    letter-spacing: 2px;
    line-height: 1;
  }
</style>
</head>
<body>

  <section class="card card--front">
    <div class="card__texture" role="img" aria-label="Dark quilted diamond pattern background"></div>
    <div class="card__frame"></div>
    <div class="brand">
      <span class="brand__name">528BUILDA</span>
      <span class="brand__tagline">Design and Renovation Firm</span>
    </div>
    <div class="website">www.yourwebsite.com</div>
  </section>

  <section class="card card--back">
    <div class="card__texture" role="img" aria-label="Dark quilted diamond pattern background"></div>
    <div class="card__frame"></div>

    <div class="back-brand">528BUILDA</div>

    <div class="person">
      <div class="person__name">Your Name</div>
      <div class="person__title">Your Title</div>
    </div>

    <ul class="contacts">
      <li class="contacts__item">
        <svg class="contacts__icon" viewBox="0 0 28 28"><circle cx="14" cy="14" r="14" fill="#d8b56a"/><path d="M9 7.5c1-.6 1.8-.3 2.3.6l1.2 2.3c.4.8.2 1.5-.5 2l-.8.6c.7 1.7 1.900 3 3.6 3.8l.6-.8c.5-.7 1.3-.9 2-.5l2.3 1.2c.9.5 1.100 1.4.5 2.3-1 1.5-2.600 2-4.300 1.300C11.8 19 9 16.2 7.7 12.1 7.1 10.3 7.6 8.6 9 7.5z" fill="#111"/></svg>
        <span>Your Phone Number</span>
      </li>
      <li class="contacts__item">
        <svg class="contacts__icon" viewBox="0 0 28 28"><circle cx="14" cy="14" r="14" fill="#d8b56a"/><g fill="none" stroke="#111" stroke-width="1.6"><circle cx="14" cy="14" r="7.5"/><ellipse cx="14" cy="14" rx="3.2" ry="7.5"/><path d="M6.5 14h15M8 10h12M8 18h12"/></g></svg>
        <span>Your Email Address</span>
      </li>
      <li class="contacts__item">
        <svg class="contacts__icon" viewBox="0 0 28 28"><circle cx="14" cy="14" r="14" fill="#d8b56a"/><rect x="7.5" y="9.5" width="13" height="9" rx="1" fill="#111"/><path d="M8 10l6 5 6-5" fill="none" stroke="#d8b56a" stroke-width="1.3"/></svg>
        <span>Your Site Here</span>
      </li>
      <li class="contacts__item">
        <svg class="contacts__icon" viewBox="0 0 28 28"><circle cx="14" cy="14" r="14" fill="#d8b56a"/><path d="M14 6.5a5.5 5.5 0 0 1 5.5 5.5c0 4-5.5 9.5-5.5 9.5S8.5 16 8.5 12A5.5 5.5 0 0 1 14 6.5z" fill="#111"/><circle cx="14" cy="12" r="2" fill="#d8b56a"/></svg>
        <span>Your Address Here<br>Your Street Name<br>Your Country</span>
      </li>
    </ul>
  </section>

</body>
</html>
```